Whitcombe Business Card Design

The name of the business is Dario Whitcombe, CPA LLC
The service that we offer is Accounting, Tax & Consulting Services. I need it to have the following items:
Dario Whitcombe, Principal
Phone Number
Email Address
Physical Address

I have attached the company logo, one in black and one in white. Please provide a design in black background and the other in white background. Please include "Accounting, Tax & Consulting Services". I want the business card to be clean and very professional.

```html
<!DOCTYPE html>
<html lang="en">
<head>
<meta charset="utf-8">
<title>Dario Whitcombe, CPA LLC – Business Card</title>
<link href="https://fonts.googleapis.com/css2?family=Montserrat:wght@500;600&family=Roboto:wght@400;500;700;900&display=swap" rel="stylesheet">
<style>
  :root {
    --stage: #dcdcdc;
    --card: #060606;
    --card-front-a: #151515;
    --card-front-b: #0b0b0b;
    --brand-red: #a11b1f;
    --brand-grey: #8d8d8d;
    --tagline-grey: #b9b9b9;
    --ink-white: #ffffff;
  }
  * { box-sizing: border-box; margin: 0; padding: 0; }
  html, body { width: 1200px; height: 900px; overflow: hidden; }
  body {
    background: var(--stage);
    position: relative;
    font-family: "Roboto", Arial, sans-serif;
  }
  .card {
    position: absolute;
    left: 233px;
    box-shadow: 0 6px 18px rgba(0,0,0,0.25);
    overflow: hidden;
  }
  /* Front */
  .card-front {
    top: 43px;
    width: 695px;
    height: 396px;
    background: var(--card-front-b);
  }
  .front-texture {
    position: absolute;
    inset: 0;
    background: radial-gradient(ellipse at 50% 45%, var(--card-front-a), var(--card-front-b) 75%);
  }
  .front-lockup {
    position: absolute;
    inset: 0;
    display: flex;
    flex-direction: column;
    align-items: center;
    justify-content: center;
    font-family: "Montserrat", Arial, sans-serif;
  }
  .brand-line {
    display: flex;
    align-items: center;
    gap: 16px;
  }
  .brand-mark {
    width: 34px; height: 34px;
    background: var(--brand-red);
    flex: none;
  }
  .brand-name {
    color: var(--brand-grey);
    font-weight: 500;
    font-size: 40px;
    letter-spacing: 0.5px;
    white-space: nowrap;
  }
  .brand-tagline {
    margin-top: 14px;
    color: var(--tagline-grey);
    font-weight: 600;
    font-size: 28px;
    letter-spacing: 3px;
    white-space: nowrap;
  }
  /* Back */
  .card-back {
    top: 461px;
    width: 700px;
    height: 400px;
    background: var(--card);
    color: var(--ink-white);
  }
  .person {
    position: absolute;
    left: 46px; top: 45px;
  }
  .person-name {
    font-weight: 700;
    font-size: 30px;
    line-height: 1.1;
  }
  .person-role {
    color: var(--brand-red);
    font-size: 19px;
    margin-top: 2px;
  }
  .address {
    position: absolute;
    left: 40px; top: 140px;
    font-size: 20.5px;
    line-height: 27px;
    font-style: normal;
  }
  .contact {
    position: absolute;
    left: 37px;
    display: flex;
    align-items: center;
    gap: 17px;
    font-size: 21.5px;
  }
  .contact-phone { top: 214px; }
  .contact-email { top: 258px; }
  .contact-icon { width: 30px; height: 30px; flex: none; }
  .back-lockup {
    position: absolute;
    left: 405px; top: 75px;
    width: 285px;
    height: 200px;
    display: flex;
    flex-direction: column;
    align-items: center;
    justify-content: center;
    font-family: "Montserrat", Arial, sans-serif;
  }
  .back-lockup .brand-line { gap: 8px; }
  .back-lockup .brand-mark { width: 16px; height: 16px; }
  .back-lockup .brand-name { font-size: 19px; letter-spacing: 0.3px; }
  .back-lockup .brand-tagline { font-size: 13.5px; letter-spacing: 1.4px; margin-top: 6px; }
  .services {
    position: absolute;
    left: 0; right: 0;
    top: 352px;
    text-align: center;
    color: var(--brand-red);
    font-weight: 900;
    font-size: 22px;
    letter-spacing: 4.4px;
    white-space: nowrap;
  }
</style>
</head>
<body>
  <section class="card card-front">
    <div class="front-texture" role="img" aria-label="Faint tiled brand pattern on black background"></div>
    <div class="front-lockup">
      <div class="brand-line">
        <span class="brand-mark"></span>
        <span class="brand-name">Dario Whitcombe, CPA LLC</span>
      </div>
      <div class="brand-tagline">CERTIFIED PUBLIC ACCOUNTANT</div>
    </div>
  </section>

  <section class="card card-back">
    <div class="person">
      <h1 class="person-name">Dario Whitcombe</h1>
      <p class="person-role">Principal</p>
    </div>
    <address class="address">
      421, Address line goes here<br>
      45552, Country Name
    </address>
    <div class="contact contact-phone">
      <svg class="contact-icon" viewBox="0 0 30 30" aria-hidden="true">
        <circle cx="15" cy="15" r="14" fill="#fff" stroke="#9a9a9a" stroke-width="1.5"/>
        <path d="M10 8.5c1-.6 1.8-.4 2.3.5l1.2 2.2c.4.8.2 1.4-.5 1.9l-.8.6c.7 1.6 1.9 2.9 3.5 3.7l.6-.8c.5-.7 1.2-.9 1.9-.5l2.2 1.2c.9.5 1.1 1.3.5 2.3-.9 1.5-2.3 2-4 1.3-3.8-1.6-6.4-4.3-7.9-8.1-.6-1.7-.1-3.1 1-4.3z" fill="#a11b1f"/>
      </svg>
      <span>(555) 014-2290</span>
    </div>
    <div class="contact contact-email">
      <svg class="contact-icon" viewBox="0 0 30 30" aria-hidden="true">
        <circle cx="15" cy="15" r="14" fill="#fff" stroke="#9a9a9a" stroke-width="1.5"/>
        <rect x="7.5" y="10" width="15" height="10.5" rx="1" fill="#a11b1f"/>
        <path d="M8 10.8l7 5.3 7-5.3M8 20l5.2-4.3M22 20l-5.2-4.3" fill="none" stroke="#fff" stroke-width="1.1"/>
      </svg>
      <span>info@whitcombe.com</span>
    </div>
    <div class="back-lockup">
      <div class="brand-line">
        <span class="brand-mark"></span>
        <span class="brand-name">Dario Whitcombe, CPA LLC</span>
      </div>
      <div class="brand-tagline">CERTIFIED PUBLIC ACCOUNTANT</div>
    </div>
    <p class="services">ACCOUNTING, TAX &amp; CONSULTING SERVICES</p>
  </section>
</body>
</html>
```